MRT Property - Business Cards

Looking for a business card & general letterhead, signage etc design for our new logo.

Colours:
000a20
0056a2
00b5ef
0088ce
68cef2

Fonts:
Poppins
Karla

Please keep look and feel of new brand - example in the zip package I sent.

```html
<!DOCTYPE html>
<html lang="en">
<head>
<meta charset="utf-8">
<title>MRT Property – Business Cards</title>
<link rel="stylesheet" href="https://fonts.googleapis.com/css2?family=Poppins:wght@400;600;700&display=swap">
<style>
  :root {
    --ink: #000a20;
    --brand-blue: #0056a2;
    --sky: #00b5ef;
    --mid-blue: #0088ce;
    --pale-sky: #68cef2;
    --white: #ffffff;
    --backdrop: #d0d0cb;
  }
  * { box-sizing: border-box; margin: 0; padding: 0; }
  html, body { width: 1200px; height: 801px; overflow: hidden; }
  body {
    background: var(--backdrop);
    font-family: "Poppins", sans-serif;
    position: relative;
  }
  .card {
    position: absolute;
    top: 246px;
    width: 540px;
    height: 309px;
    background: var(--brand-blue);
    border-bottom: 4px solid var(--sky);
    overflow: hidden;
    box-shadow: 0 14px 30px rgba(0, 10, 32, 0.28);
  }
  .card--front { left: 40px; }
  .card--back { left: 620px; }

  .front-emblem-area {
    position: absolute;
    top: 0;
    right: 0;
    width: 330px;
    height: 230px;
    background: radial-gradient(ellipse at 70% 20%, var(--mid-blue) 0%, #0a4f98 45%, #063a78 80%, var(--brand-blue) 100%);
    border-bottom-left-radius: 100% 90%;
  }

  .front-details {
    position: absolute;
    left: 34px;
    bottom: 26px;
    color: var(--white);
  }
  .wordmark {
    font-family: "Poppins", sans-serif;
    font-weight: 700;
    color: var(--white);
    letter-spacing: 0.02em;
    line-height: 1;
  }
  .front-details .wordmark { font-size: 30px; margin-bottom: 18px; }
  .holder-name {
    font-weight: 700;
    font-size: 19px;
    color: var(--sky);
    line-height: 1.1;
  }
  .holder-title {
    font-size: 11.5px;
    font-weight: 400;
    margin-bottom: 10px;
  }
  .contact-list { list-style: none; font-size: 11px; line-height: 1.55; }
  .contact-list li { display: flex; align-items: center; gap: 7px; }
  .contact-list svg { width: 10px; height: 10px; flex: none; }
  .address { font-size: 11px; line-height: 1.45; margin-top: 8px; }

  .back-pattern-area {
    position: absolute;
    inset: 0;
    background: linear-gradient(135deg, #062d64 0%, #0a4a92 45%, #0a73c8 75%, var(--mid-blue) 100%);
  }
  .back-brand {
    position: absolute;
    right: 60px;
    top: 50%;
    transform: translateY(-50%);
    display: flex;
    align-items: center;
    gap: 12px;
  }
  .back-brand .dot {
    width: 26px;
    height: 26px;
    border-radius: 50%;
    background: var(--pale-sky);
  }
  .back-brand .wordmark { font-size: 30px; }
</style>
</head>
<body>

  <section class="card card--front" aria-label="Business card front">
    <div class="front-emblem-area" role="img" aria-label="Large brand emblem in layered blues"></div>
    <div class="front-details">
      <p class="wordmark">MRT PROPERTY</p>
      <p class="holder-name">DANA HALE</p>
      <p class="holder-title">Founder &amp; Principal</p>
      <ul class="contact-list">
        <li>
          <svg viewBox="0 0 10 10"><path d="M2 1 L4 1 L4.6 3 L3.5 3.8 C4 5 5 6 6.2 6.5 L7 5.4 L9 6 L9 8 C5 8.5 1.5 5 2 1 Z" fill="var(--sky)"/></svg>
          +1- 555-014-2290
        </li>
        <li>
          <svg viewBox="0 0 10 10"><rect x="0.8" y="2" width="8.4" height="6" fill="none" stroke="var(--sky)" stroke-width="1"/><path d="M1 2.3 L5 5.5 L9 2.3" fill="none" stroke="var(--sky)" stroke-width="1"/></svg>
          info@mrtproperty.com
        </li>
        <li>
          <svg viewBox="0 0 10 10"><circle cx="5" cy="5" r="4.2" fill="var(--sky)"/></svg>
          www.mrtproperty.com
        </li>
      </ul>
      <p class="address">4120 North Elm Avenue<br>#27, Suite Riverbend</p>
    </div>
  </section>

  <section class="card card--back" aria-label="Business card back">
    <div class="back-pattern-area" role="img" aria-label="Repeating brand pattern in graded blues"></div>
    <div class="back-brand">
      <span class="dot"></span>
      <p class="wordmark">MRT PROPERTY</p>
    </div>
  </section>

</body>
</html>
```